Moravel Aesthetic Doctor

I require an elegant, luxurious looking business card for my aesthetic business. I am a doctor and that will set me aside from competitors. I am planning to provide home and spa based treatments to clients with high expectations. I have attached my logo.

```html
<!DOCTYPE html>
<html lang="en">
<head>
<meta charset="utf-8">
<title>Moravel Aesthetic Doctor — Business Card</title>
<link rel="stylesheet" href="https://fonts.googleapis.com/css2?family=Roboto:wght@300;400&display=swap">
<style>
  :root {
    --stage: #3a3b3d;
    --card: #1d1e20;
    --card-edge: #2a2b2e;
    --sky: #4fb4e9;
    --silver: #8d9095;
    --mist: #c9ccd1;
    --rule: #6b6e73;
  }
  * { box-sizing: border-box; margin: 0; padding: 0; }
  html, body {
    width: 799px; height: 1200px; overflow: hidden;
    background: var(--stage);
    font-family: "Roboto", Arial, sans-serif;
  }
  .stage {
    position: relative; width: 799px; height: 1200px;
    display: flex; flex-direction: column; align-items: center; justify-content: space-around;
  }
  .card {
    position: relative; width: 620px; height: 360px;
    background: var(--card);
    border: 1px solid var(--card-edge);
    border-radius: 6px;
    overflow: hidden;
  }
  /* Front */
  .card--front { display: flex; align-items: center; justify-content: center; }
  .front-mark { display: flex; align-items: center; gap: 18px; }
  .front-mark__ring {
    width: 64px; height: 64px; border-radius: 50%;
    border: 3px solid var(--silver);
  }
  .front-mark__name {
    font-weight: 300; font-size: 44px; letter-spacing: 4px; color: var(--silver);
  }
  /* Back */
  .brand {
    position: absolute; left: 40px; top: 40px;
    display: flex; align-items: center; gap: 16px;
  }
  .brand__ring {
    width: 58px; height: 58px; border-radius: 50%;
    border: 2px solid var(--mist);
  }
  .brand__name {
    font-weight: 300; font-size: 30px; letter-spacing: 2px; color: var(--sky);
  }
  .holder { position: absolute; left: 40px; top: 168px; }
  .holder__name { font-weight: 300; font-size: 24px; color: var(--mist); }
  .holder__post { font-size: 11px; margin-left: 6px; letter-spacing: .5px; }
  .holder__diploma { font-weight: 400; font-size: 15px; color: var(--sky); margin-top: 4px; }
  .contacts {
    position: absolute; left: 40px; top: 246px; right: 40px;
    display: flex; gap: 26px; font-size: 15px; color: var(--mist); font-weight: 300;
  }
  .contact { display: flex; align-items: center; gap: 8px; white-space: nowrap; }
  .contact svg { width: 18px; height: 18px; flex: none; }
  .contact svg * { fill: none; stroke: var(--sky); stroke-width: 1.4; }
  .divider {
    position: absolute; left: 40px; right: 40px; top: 226px;
    border-top: 1px solid var(--rule);
  }
  .web {
    position: absolute; left: 40px; top: 290px;
  }
  .social-band {
    position: absolute; right: 0; bottom: 26px; width: 150px; height: 10px;
    background: var(--sky);
  }
  .social-band__pill {
    position: absolute; right: 40px; bottom: 0; width: 92px; height: 32px;
    background: var(--sky); border-radius: 16px 16px 0 16px;
  }
</style>
</head>
<body>
<main class="stage">
  <section class="card card--front" aria-label="Card front">
    <div class="front-mark">
      <span class="front-mark__ring"></span>
      <span class="front-mark__name">Moravel</span>
    </div>
  </section>

  <section class="card card--back" aria-label="Card back">
    <div class="brand">
      <span class="brand__ring"></span>
      <span class="brand__name">Moravel Aesthetic Doctor</span>
    </div>

    <div class="holder">
      <p class="holder__name">Dr Liesel Marrow<span class="holder__post">MRCPCH MD</span></p>
      <p class="holder__diploma">Australasian Diploma of Aesthetic Medicine</p>
    </div>

    <div class="divider"></div>

    <div class="contacts">
      <span class="contact">
        <svg viewBox="0 0 18 18"><circle cx="9" cy="9" r="8"/><path d="M6 5l2 2-1 1.2c.6 1.3 1.5 2.2 2.8 2.8L11 10l2 2-1.2 1.2C8.5 12.8 5.2 9.5 4.8 6.2z"/></svg>
        0800 555 014
      </span>
      <span class="contact">
        <svg viewBox="0 0 18 18"><rect x="2" y="4" width="14" height="10" rx="1"/><path d="M2 4.5l7 5.5 7-5.5"/></svg>
        liesel@moravel.co.nz
      </span>
    </div>

    <div class="contacts web">
      <span class="contact">
        <svg viewBox="0 0 18 18"><circle cx="9" cy="9" r="7.5"/><ellipse cx="9" cy="9" rx="3.2" ry="7.5"/><path d="M1.5 9h15M3 5h12M3 13h12"/></svg>
        www.moravel.co.nz
      </span>
    </div>

    <div class="social-band" aria-hidden="true"></div>
    <div class="social-band__pill" aria-hidden="true" style="bottom:26px;"></div>
  </section>
</main>
</body>
</html>
```